Cash Balance Retirement Plan Services Page

We are looking to have a services/landing page created for one of our offerings. The goal of the page is to explain a relatively complex service (advanced retirement plan) by highlighting the benefits and uses for the plan such that it tells a story that encourages individuals and businesses that would benefit from the plans to reach out.

The page will be used both as a landing page (though secondarily) and as a page that many of our partners will show to their clients in order to generate interest. We help other people closes these deals so we want it to handle both.

Overall, we would want the page to incorporate the following sections/areas.
1. Headline and a place for a video at the top
2. Explanation of what a cash balance plan is (a paragraph or two)
3. These five benefits: These are the 7 we usually use, but only include five at a time so only need room for five.
a. Highest Tax Deductible Contributions Allowed
b. Significantly reduce your taxes
c. Potential Negative “Net Cost”
d. Owner & Executive Weighted Benefits
e. Retain and Attract Top Talen
f. Catch Up On decades of low retirement savings in a matter of years
g. Potential for life time income
4. A section comparing the contribution limits allowed for each plan type (Please see attached image as an example).
5. A place for a table of contribution amounts (This will just be an image. Also, attached).
6. A place for a compare table
6. Who should consider such a plan
7. Occasional banners for call to actions
8. FAQ

Our primary audience for this project are successful small business owners with a particular focus on medical professionals (doctors, chiropractors, dentists, plastic surgeons, etc.). In generally, they will be between 45 and 65 years old and earn $150k or more.

Because we work a lot with financial, business strategy, and insurance based products that require a significant investment by the client trust, professionalism, and sophistication are important attributes we wish to portray in the design of the page. Our preferred colors are blue or green. Though we are still working on figuring out the color scheme so your input as a designer is welcomed as your creativity can help us communicate the attributes we seek to embody for our clients.

In the attached document, I have included some additional information about the service itself if it helps to have some context, as well as a more flushed out outline of the details above.

Importantly, I am not a marketer so any creative input is always welcome if there is a best practice we are not incorporating in either our design requests or outline.

Here is the URL for our current page: https://www.brightvaleadvisors.com/physicianplan

Please don't let this page be your muse. We're trying to get away from it for a reason :) But it still will hopefully provide some helpful information, copy examples, and context.

Additionally, please don't feel like you need to read the full cash balance explanation. That's only if context will be helpful.

We are also going through a rebranding so please don't rely on the colors from the BrightValeAdvisors logo you may see on the website. I've attached two sample logos for the rebrand for context.

```html
<!DOCTYPE html>
<html lang="en">
<head>
<meta charset="utf-8">
<title>Brightvale – Cash Balance Plan</title>
<link href="https://fonts.googleapis.com/css2?family=Orbitron:wght@500;600;700&family=Lato:wght@400;700&family=Roboto:wght@400;700&display=swap" rel="stylesheet">
<style>
:root{
  --ink:#111418;
  --dark:#161616;
  --navy:#1c2f9e;
  --blue:#2a5bd7;
  --sky:#8fd3f4;
  --mid:#4f9de6;
  --text:#4a4f57;
  --muted:#6b7078;
  --pale:#eef3f9;
  --faq:#f1f2f5;
  --green:#1fa23d;
  --lime:#7cc243;
  --bar-light:#8ab9ee;
  --bar-dark:#1d5fcc;
  --white:#ffffff;
}
*{box-sizing:border-box;margin:0;padding:0}
html,body{width:1200px;height:4808px;overflow:hidden}
body{position:relative;font-family:'Lato',sans-serif;color:var(--text);background:var(--white)}
.abs{position:absolute}
.display{font-family:'Orbitron',sans-serif;color:var(--ink);font-weight:600}
.btn{position:absolute;display:flex;align-items:center;justify-content:center;border-radius:30px;font-family:'Orbitron',sans-serif;font-size:15px;color:#fff;background:linear-gradient(90deg,var(--sky),var(--blue))}

/* top bar */
.topbar{position:absolute;left:0;top:0;width:1200px;height:82px;background:var(--dark);color:#fff}
.brand{position:absolute;display:flex;align-items:center;gap:12px;font-family:'Orbitron',sans-serif;font-weight:600;color:#fff}
.brand .dot{border-radius:50%;background:linear-gradient(135deg,var(--sky),var(--navy))}
.contact-item{position:absolute;top:18px;display:flex;align-items:center;gap:12px;font-size:15px;line-height:1.2}
.contact-item .ico{width:34px;height:34px;border-radius:50%;background:var(--sky);display:flex;align-items:center;justify-content:center}
.contact-item b{display:block;font-size:14px}
.socials{position:absolute;display:flex;gap:8px}
.socials span{width:30px;height:30px;border-radius:50%;background:#cfd8e3}
.socials.top span:first-child{background:var(--sky)}

/* nav */
.nav{position:absolute;left:0;top:82px;width:1200px;height:68px;background:linear-gradient(90deg,var(--sky),#4e8fe3 55%,var(--navy))}
.nav ul{position:absolute;left:148px;top:24px;display:flex;gap:62px;list-style:none;color:#fff;font-size:14px}
.search{position:absolute;left:788px;top:10px;width:296px;height:48px;border-radius:26px;background:#f1f4f8;font-size:14px;color:var(--muted);padding:15px 26px}
.search i{position:absolute;right:6px;top:5px;width:38px;height:38px;border-radius:50%;background:var(--mid)}

/* hero */
.hero{position:absolute;left:0;top:150px;width:1200px;height:617px;background:linear-gradient(180deg,#f3f6fa,#e6edf5)}
.hero-photo{position:absolute;left:532px;top:0;width:668px;height:617px;background:radial-gradient(ellipse at 55% 60%,#d9dde2,#c2c9d2 45%,transparent 75%)}
.hero .eyebrow{position:absolute;left:112px;top:165px;display:flex;align-items:center;gap:14px;font-size:18px;color:var(--ink)}
.hero .eyebrow::before{content:"";width:62px;height:3px;background:var(--blue)}
.hero h1{position:absolute;left:110px;top:190px;font-family:'Orbitron',sans-serif;font-weight:700;font-size:54px;color:var(--ink)}
.hero p{position:absolute;left:112px;top:268px;width:420px;font-size:14.5px;line-height:1.75;color:#333}
.watch{position:absolute;left:298px;top:352px;display:flex;align-items:center;gap:14px;font-family:'Orbitron',sans-serif;font-size:14px;color:var(--navy)}
.watch i{width:44px;height:44px;border-radius:50%;background:#fff;border:3px solid #c8dcf4;display:flex;align-items:center;justify-content:center}

/* about */
.about-photo{position:absolute;left:112px;top:838px;width:453px;height:476px;border-radius:60px 60px 60px 60px;background:linear-gradient(160deg,#d8d2c8,#b7bcc4 55%,#8f9aa8)}
.about-badge{position:absolute;left:472px;top:1207px;width:120px;height:120px;border-radius:50%;background:linear-gradient(135deg,#4f86e0,var(--navy));border:6px solid #fff}
.about h2{position:absolute;left:620px;top:888px;width:480px;font-size:36px;line-height:1.25}
.about p{position:absolute;left:620px;top:995px;width:460px;font-size:13.5px;line-height:1.85;color:#333}

/* benefits */
.benefits{position:absolute;left:0;top:1452px;width:1200px;height:778px;background:linear-gradient(100deg,#7cc9f0,#4a8fe0 45%,#2753c4)}
.benefits h2{position:absolute;left:0;width:1200px;top:56px;text-align:center;font-size:36px;color:#fff}
.arrow{position:absolute;width:24px;height:24px;border-radius:50%;background:#fff;display:flex;align-items:center;justify-content:center}
.card{position:absolute;top:134px;width:231px;height:377px;background:#fff;border-radius:18px;overflow:hidden;text-align:center}
.card .pic{height:187px;background:linear-gradient(160deg,#c6d3df,#8fa7c1)}
.card h3{font-family:'Orbitron',sans-serif;font-weight:500;font-size:13px;line-height:1.45;color:var(--ink);margin:18px 10px 10px;height:42px;display:flex;align-items:center;justify-content:center}
.card p{font-size:13.5px;line-height:1.75;color:var(--muted);margin:0 14px;height:72px;overflow:hidden}
.card a{display:inline-block;margin-top:12px;font-size:13.5px;color:var(--navy);text-decoration:underline}

/* chart */
.chart-card{position:absolute;left:112px;top:2043px;width:978px;height:633px;background:#fff;border-radius:50px;box-shadow:0 10px 40px rgba(30,60,140,.12)}
.chart-card h2{position:absolute;left:0;width:978px;top:40px;text-align:center;font-size:36px}
.chart{position:absolute;left:0;top:0;font-family:'Roboto',Arial,sans-serif;font-weight:700;font-size:16px;color:var(--ink)}
.chart-card p{position:absolute;left:70px;top:497px;width:838px;text-align:center;font-size:14px;line-height:1.85;color:#333}

/* table */
.table-title{position:absolute;left:0;top:2756px;width:1200px;text-align:center;font-size:36px;line-height:1.35}
.contrib{position:absolute;left:192px;top:2879px;width:821px;border-collapse:collapse;font-family:'Roboto',Arial,sans-serif;font-size:21px;box-shadow:0 0 6px rgba(0,0,0,.25)}
.contrib th{background:var(--navy);color:#fff;text-align:left;font-weight:700;vertical-align:top;padding:8px 8px;height:120px;line-height:1.3;border-right:1px solid #c7cce0}
.contrib td{padding:0 8px;height:37.5px;color:#222;border-right:1px solid #b7bfd8}
.contrib tr:nth-child(odd) td{background:#cfd6ec}
.contrib tr:nth-child(even) td{background:#e8ebf6}
.contrib td.strong{font-weight:700;color:#000}

/* who */
.who{position:absolute;left:0;top:3363px;width:1200px;height:408px;background:linear-gradient(100deg,#73c2ee,#3f7fdc 50%,#2450c0)}
.who h2{position:absolute;left:0;width:1200px;top:78px;text-align:center;font-size:36px;color:#fff}
.who p{position:absolute;left:150px;width:900px;top:152px;text-align:center;color:#eef4ff;font-size:14px;line-height:1.85}
.who .btn-light{position:absolute;left:511px;top:277px;width:166px;height:58px;border-radius:30px;background:#fff;color:var(--navy);font-family:'Orbitron',sans-serif;font-size:15px;display:flex;align-items:center;justify-content:center}

/* faq */
.faq-title{position:absolute;left:0;width:1200px;top:3842px;text-align:center;font-size:30px}
.faq-item{position:absolute;left:200px;width:798px;height:60px;border-radius:30px;background:var(--faq);display:flex;align-items:center;font-family:'Orbitron',sans-serif;font-size:16px;color:var(--ink);font-weight:500}
.faq-item .num{width:42px;height:42px;margin:0 30px 0 10px;border-radius:50%;background:var(--navy);color:#fff;display:flex;align-items:center;justify-content:center;font-size:16px;font-weight:700}
.faq-item.open .num{background:#d6ecfb;color:#fff}
.faq-item.open{background:#f6f7f9}
.faq-item .toggle{position:absolute;right:28px;top:20px;width:18px;height:18px}
.faq-answer{position:absolute;left:222px;top:4010px;width:680px;font-size:14px;line-height:1.85;color:var(--muted)}

/* footer */
.footer{position:absolute;left:0;top:4437px;width:1200px;height:371px;background:var(--dark);color:#fff}
.footer h4{position:absolute;top:56px;font-family:'Orbitron',sans-serif;font-weight:500;font-size:19px}
.footer ul{position:absolute;list-style:none;font-size:14px;line-height:30px}
.footer .row{display:flex;gap:12px;align-items:flex-start}
.news-input{position:absolute;left:815px;top:113px;width:275px;height:42px;border-radius:22px;background:#fff;color:#999;font-size:14px;padding:12px 22px}
.news-btn{position:absolute;left:815px;top:166px;width:275px;height:43px;border-radius:22px;background:var(--navy);color:#fff;font-size:16px;display:flex;align-items:center;justify-content:center}
.copy{position:absolute;left:0;width:1200px;top:310px;text-align:center;font-size:14px}
</style>
</head>
<body>

<header class="topbar">
  <div class="brand" style="left:112px;top:12px;font-size:24px"><span class="dot" style="width:56px;height:56px"></span>BRIGHTVALE</div>
  <div class="contact-item" style="left:408px">
    <span class="ico"><svg width="16" height="12" viewBox="0 0 16 12"><rect x="0.5" y="0.5" width="15" height="11" fill="none" stroke="#fff"/><path d="M1 1l7 6 7-6" fill="none" stroke="#fff"/></svg></span>
    <div><b>Email</b>info@brightvale.com</div>
  </div>
  <div class="contact-item" style="left:678px">
    <span class="ico"><svg width="16" height="16" viewBox="0 0 24 24"><path d="M6.6 10.8a15 15 0 006.6 6.6l2.2-2.2c.3-.3.7-.4 1-.2 1.1.4 2.3.6 3.6.6.6 0 1 .4 1 1V20c0 .6-.4 1-1 1A17 17 0 013 4c0-.6.4-1 1-1h3.5c.6 0 1 .4 1 1 0 1.2.2 2.4.6 3.6.1.3 0 .7-.2 1z" fill="#fff"/></svg></span>
    <div><b>Call Us</b>+1 888 888 8888</div>
  </div>
  <div class="socials top" style="left:932px;top:26px"><span></span><span></span><span></span><span></span></div>
</header>

<nav class="nav">
  <ul><li>Home</li><li>Our Services</li><li>Our Blog</li><li>News</li><li>Contact Us</li></ul>
  <div class="search">Search<i></i></div>
</nav>

<section class="hero">
  <div class="hero-photo" role="img" aria-label="Portrait of a smiling physician in a white coat"></div>
  <div class="eyebrow">Welcome To</div>
  <h1>Brightvale</h1>
  <p>Are you healthy enough that you are at risk of outliving your retirement savings?</p>
  <div class="btn" style="left:112px;top:343px;width:168px;height:59px">Get Started</div>
  <div class="watch"><i><svg width="14" height="14" viewBox="0 0 14 14"><path d="M3 1l10 6-10 6z" fill="#2a5bd7"/></svg></i>Watch Video</div>
</section>

<section class="about">
  <div class="about-photo" role="img" aria-label="Chiropractor treating a patient's shoulder"></div>
  <div class="about-badge"></div>
  <h2 class="display">What a cash balance plan</h2>
  <p>A cash balance plan is a retirement plan specifically for small business owners, doctors, lawyers, and other high-income professionals. It allows for the highest tax-deductible contribution limits in the market, and the older you get, the higher those limits go. You then get an option for guaranteed income for life or a one time, lump payout. Why this matters: The IRS has a number of special types of retirement plans they offer people to use that come with tax-advantages. Usually, this is pre-tax contributions (also called, tax deferred). In essence, this means that the</p>
  <div class="btn" style="left:620px;top:1241px;width:169px;height:59px">Learn More</div>
</section>

<section class="benefits">
  <h2 class="display">Our Benefits</h2>
  <div class="arrow" style="left:44px;top:309px"><svg width="10" height="10" viewBox="0 0 10 10"><path d="M6.5 1.5L3 5l3.5 3.5" fill="none" stroke="#4a8fe0" stroke-width="1.6"/></svg></div>
  <div class="arrow" style="left:1134px;top:309px;background:#5fb6ef"><svg width="10" height="10" viewBox="0 0 10 10"><path d="M3.5 1.5L7 5 3.5 8.5" fill="none" stroke="#fff" stroke-width="1.6"/></svg></div>

  <article class="card" style="left:110px">
    <div class="pic" role="img" aria-label="Chiropractor adjusting a patient's back"></div>
    <h3>Highest Tax Deductible Contributions Allowed</h3>
    <p>Most retirement plans in the US (IRAs, 401(k), SEP) allow $7k, $27k, or $61k</p>
    <a>Learn More</a>
  </article>
  <article class="card" style="left:358px">
    <div class="pic" role="img" aria-label="Dentist reviewing notes with an assistant"></div>
    <h3>Significantly reduce your taxes</h3>
    <p>contributions are 100% tax deductible. That means an individual who</p>
    <a>Learn More</a>
  </article>
  <article class="card" style="left:606px">
    <div class="pic" role="img" aria-label="Dental team preparing a treatment room"></div>
    <h3>Potential Negative “Net Cost”</h3>
    <p>Many businesses are unable to contribute to their own retirement because they</p>
    <a>Learn More</a>
  </article>
  <article class="card" style="left:855px">
    <div class="pic" role="img" aria-label="Dentist examining a young patient"></div>
    <h3>Owner &amp; Executive Weighted Benefits</h3>
    <p>These plans allow greater contribution for owners and executives who are...</p>
    <a>Learn More</a>
  </article>
</section>

<section class="chart-card">
  <h2 class="display">contribution limits allowed for each</h2>
  <svg class="chart" width="978" height="500" viewBox="0 0 978 500">
    <g font-family="Roboto, Arial, sans-serif" font-weight="700" font-size="16" fill="#111418" text-anchor="middle">
      <text x="149" y="326">Annual</text><text x="149" y="346">Contributio</text><text x="149" y="366">ns</text><text x="149" y="386">Limits</text>
      <rect x="224" y="372" width="67" height="17" fill="#7cc243"/>
      <text x="257" y="339">$6,000</text><text x="257" y="359">($7000)</text><text x="257" y="411">IRA</text>
      <rect x="371" y="349" width="66" height="38" fill="#1fa23d"/>
      <text x="404" y="316">$20,500</text><text x="404" y="336">($27,000)</text><text x="404" y="411">401(k)</text>
      <rect x="519" y="297" width="65" height="90" fill="#8ab9ee" stroke="#c9def7"/>
      <text x="551" y="286">$61,000</text><text x="551" y="411">Profit</text><text x="551" y="431">Sharin</text><text x="551" y="451">g</text>
      <rect x="664" y="146" width="67" height="241" fill="#1d5fcc" stroke="#9fc1ee"/>
      <text x="697" y="135">$416,000</text><text x="697" y="411">Cash</text><text x="697" y="431">Balance</text><text x="697" y="451">Plan</text>
      <g font-weight="400" font-size="14">
        <text x="825" y="191">*Your</text><text x="825" y="209">contribution</text><text x="825" y="227">limits will be</text><text x="825" y="245">based on age</text><text x="825" y="263">and salary</text><text x="825" y="281">and may not</text><text x="825" y="299">reach the max</text><text x="825" y="317">contribution</text><text x="825" y="335">amount.</text>
      </g>
    </g>
  </svg>
  <p>Lorem ipsum dolor sit amet, consectetur adipiscing elit, sed do eiusmod tempor incididunt ut labore et dolore magna aliqua. Quis ipsum suspendisse ultrices gravida. Risus commodo viverra maecenas accumsan lacus vel facilisis. Lorem ipsum dolor sit amet, consectetur adipiscing elit, sed do eiusmod tempor incididunt ut labore et dolore magna aliqua. Quis ipsum suspendisse ultrices gravida. Risus commodo</p>
</section>

<h2 class="display table-title">Table Of Contribution<br>Amounts</h2>
<table class="contrib">
  <thead><tr><th>Starting<br>Plan at Age:</th><th>Max<br>Monthly<br>Retirement<br>Benefit:</th><th>Lump Sum<br>at<br>Retirement:</th><th>Illustrative<br>Contribution<br>Limits:</th><th>Estimated<br>Tax<br>Savings:</th><th>“Net Cost”<br>after Tax<br>Savings:</th></tr></thead>
  <tbody>
    <tr><td>40</td><td>$20,417</td><td>$2,959,124</td><td class="strong">$141,358</td><td>$56,543</td><td>$84,814</td></tr>
    <tr><td>45</td><td>$20,417</td><td>$2,959,124</td><td class="strong">$178,753</td><td>$71,501</td><td>$107,252</td></tr>
    <tr><td>50</td><td>$20,417</td><td>$2,959,124</td><td class="strong">$246,962</td><td>$98,784</td><td>$148,177</td></tr>
    <tr><td>55</td><td>$20,417</td><td>$2,959,124</td><td class="strong">$382,181</td><td>$152,872</td><td>$229,308</td></tr>
    <tr><td>60</td><td>$10,208</td><td>$1,479,561</td><td class="strong">$400,418</td><td>$160,192</td><td>$240,225</td></tr>
  </tbody>
</table>
<div class="btn" style="left:532px;top:3234px;width:168px;height:56px">Learn More</div>

<section class="who" role="img" aria-label="Surgical team at work, tinted blue">
  <h2 class="display">Who should consider such a plan</h2>
  <p>Lorem ipsum dolor sit amet, consectetur adipiscing elit, sed do eiusmod tempor incididunt ut labore et dolore magna aliqua. Quis ipsum suspendisse ultrices gravida. Risus commodo viverra maecenas accumsan lacus vel facilisis. Lorem ipsum dolor sit amet, consectetur adipiscing elit, sed do eiusmod tempor incididunt ut labore et dolore magna aliqua. Quis ipsum suspendisse ultrices gravida. Risus commodo viverra maecenas accumsan lacus vel facilisis.</p>
  <div class="btn-light">Learn More</div>
</section>

<h2 class="display faq-title">Frequently Asked Questions</h2>
<div class="faq-item open" style="top:3928px"><span class="num">01</span>What is your company slogan or mission statement?<svg class="toggle" viewBox="0 0 18 18"><rect x="2" y="8" width="14" height="2" fill="#8fd3f4"/></svg></div>
<p class="faq-answer">We help our clients protect their financial futures, build generational wealth, and open doors for the highest allowable tax-deductible contributions for their retirement savings as designed by the federal government. By helping their businesses reduce their tax burden, they're better able to provide for themselves and their employees.</p>
<div class="faq-item" style="top:4137px"><span class="num">02</span>What is your goal with this content?<svg class="toggle" viewBox="0 0 18 18"><path d="M8 2h2v14H8zM2 8h14v2H2z" fill="#1c2f9e"/></svg></div>
<div class="faq-item" style="top:4227px"><span class="num">03</span>What are the unique selling points of your company?<svg class="toggle" viewBox="0 0 18 18"><path d="M8 2h2v14H8zM2 8h14v2H2z" fill="#1c2f9e"/></svg></div>
<div class="faq-item" style="top:4311px"><span class="num">04</span>Is there a specific tone of voice you want?<svg class="toggle" viewBox="0 0 18 18"><path d="M8 2h2v14H8zM2 8h14v2H2z" fill="#1c2f9e"/></svg></div>

<footer class="footer">
  <div class="brand" style="left:112px;top:65px;font-size:21px"><span class="dot" style="width:48px;height:48px"></span>BRIGHTVALE</div>
  <div class="socials" style="left:146px;top:136px"><span style="background:#fff"></span><span style="background:#fff"></span><span style="background:#fff"></span><span style="background:#fff"></span></div>

  <h4 style="left:371px">Quick Link</h4>
  <ul style="left:379px;top:96px"><li>Home</li><li>Our Services</li><li>Our Blog</li><li>News</li><li>Contact Us</li></ul>

  <h4 style="left:543px">Contact Us</h4>
  <ul style="left:543px;top:102px;width:230px;line-height:24px">
    <li class="row"><svg width="12" height="16" viewBox="0 0 12 16" style="margin-top:4px;flex:none"><path d="M6 0a6 6 0 00-6 6c0 4.5 6 10 6 10s6-5.5 6-10a6 6 0 00-6-6zm0 8.2A2.2 2.2 0 116 3.8a2.2 2.2 0 010 4.4z" fill="#fff"/></svg><span>Lorem ipsum dolor sit amet consectetur</span></li>
    <li class="row" style="margin-top:10px"><svg width="14" height="11" viewBox="0 0 14 11" style="margin-top:7px;flex:none"><rect width="14" height="11" fill="#fff"/><path d="M0 0l7 6 7-6" fill="none" stroke="#161616"/></svg><span>info@brightvale.com</span></li>
    <li class="row" style="margin-top:10px"><svg width="13" height="13" viewBox="0 0 24 24" style="margin-top:6px;flex:none"><path d="M6.6 10.8a15 15 0 006.6 6.6l2.2-2.2c.3-.3.7-.4 1-.2 1.1.4 2.3.6 3.6.6.6 0 1 .4 1 1V20c0 .6-.4 1-1 1A17 17 0 013 4c0-.6.4-1 1-1h3.5c.6 0 1 .4 1 1 0 1.2.2 2.4.6 3.6.1.3 0 .7-.2 1z" fill="#fff"/></svg><span>+1 888 888 8888</span></li>
  </ul>

  <h4 style="left:815px">Sign up our Newsletter</h4>
  <div class="news-input">Email</div>
  <div class="news-btn">Submit</div>

  <p class="copy">©Copyrights 2022 &nbsp;Brightvale | &nbsp;All Rights Reserved</p>
</footer>

</body>
</html>
```